Priority Goals poster for school year

We are an elementary school and the past two years have had you help us to design a "poster" that illustrates our goal of the coming year. I am attaching our last year's one, along with some photos of our (ver rough) thinking for next years. The priority goal at top remains the same. Can't wait to see your genius ideas! :)

Target Market(s)

Staff of an elementary school and parents to some (informative) extent as well.

Colors
296eb1
6094c6
fbed22
fbee3f

Requirements
Must have
• items from the white board picture we have attached

```html
<!DOCTYPE html>
<html lang="en">
<head>
<meta charset="utf-8">
<title>Priority Goals Poster</title>
<link href="https://fonts.googleapis.com/css2?family=Montserrat:wght@500;600;700;800&display=swap" rel="stylesheet">
<style>
  :root {
    --navy: #2a3a96;
    --blue-dark: #2b4596;
    --blue-light: #6fa6d6;
    --yellow: #ecc633;
    --ring: #eec82a;
    --white: #ffffff;
    --page: #dfe3e6;
    --mist: #eef0f6;
  }
  * { margin: 0; padding: 0; box-sizing: border-box; }
  html, body { width: 1144px; height: 1200px; overflow: hidden; }
  body { background: var(--page); font-family: "Montserrat", sans-serif; position: relative; }

  .poster { position: absolute; left: 192px; top: 21px; width: 760px; height: 1158px; background: var(--white); overflow: hidden; }
  .abs { position: absolute; white-space: nowrap; }

  .backdrop { left: 0; top: 217px; width: 760px; height: 707px;
    background: linear-gradient(180deg, var(--mist) 0%, #f6f7fb 55%, var(--white) 100%); }

  .year { left: 0; top: 28px; width: 560px; text-align: center; font-size: 62px; font-weight: 800; color: var(--navy); line-height: 1; letter-spacing: -1px; }
  .title-band { left: 0; top: 89px; width: 760px; height: 59px; background: var(--navy); }
  .title { left: 11px; top: 93px; font-size: 50px; font-weight: 800; color: var(--white); line-height: 1; letter-spacing: 0; }
  .intro-band { left: 0; top: 148px; width: 760px; height: 62px; background: var(--yellow); }
  .intro { left: 12px; top: 155px; width: 520px; font-size: 18px; font-weight: 600; color: var(--navy); line-height: 22px; white-space: normal; }

  .school-mark { left: 548px; top: 40px; width: 204px; height: 210px; background: var(--white); border-radius: 14px;
    display: flex; flex-direction: column; align-items: center; justify-content: center; gap: 8px; }
  .school-mark .dot { width: 64px; height: 64px; border-radius: 50%; background: var(--yellow); }
  .school-mark .name { font-size: 21px; font-weight: 800; color: var(--navy); text-align: center; line-height: 24px; }

  .wheel { left: 0; top: 0; }

  .goal { font-size: 16px; font-weight: 500; line-height: 20px; }
  .goal.on-dark { color: var(--white); }
  .goal.on-yellow { color: var(--navy); }
  .tag-dark { background: var(--navy); color: var(--white); padding: 0 4px; }
  .tag-light { background: var(--white); color: var(--navy); padding: 0 4px; }
  .goal ul { list-style: none; }
  .goal li::before { content: ""; display: inline-block; width: 8px; height: 8px; border-radius: 50%; margin-right: 5px; vertical-align: 2px; }
  .on-dark li::before { background: var(--white); }
  .on-yellow li::before { background: var(--navy); }

  .voices { left: 192px; top: 338px; line-height: 25px; }
  .broaden { left: 362px; top: 325px; }
  .staff { left: 500px; top: 416px; }
  .staff p + p { margin-top: 8px; }
  .communicate { left: 525px; top: 545px; line-height: 21px; }
  .communicate li { font-size: 14px; line-height: 23px; }
  .communicate li:nth-child(1) { margin-left: 17px; }
  .communicate li:nth-child(2) { margin-left: 33px; }
  .communicate li:nth-child(3) { margin-left: 42px; }
  .build { left: 435px; top: 688px; line-height: 21px; }
  .build strong { font-weight: 700; font-size: 17px; }
  .build li { font-size: 14px; margin-left: 0; }
  .wellness { left: 243px; top: 759px; font-size: 14px; line-height: 20px; }
  .wellness .tag-dark { font-size: 16px; font-weight: 700; margin-left: 29px; }
  .intentional { left: 109px; top: 669px; }
  .small-steps { left: 100px; top: 505px; line-height: 24px; }

  .promises { left: 0; top: 938px; width: 760px; text-align: center; font-size: 46px; font-weight: 800; color: var(--navy); letter-spacing: -0.5px; line-height: 1; }
  .promises-sub { left: 0; top: 991px; width: 760px; text-align: center; font-size: 26px; font-weight: 500; color: var(--navy); line-height: 1; }

  .footer-strip { left: 0; top: 1028px; width: 760px; height: 13px; background: var(--yellow); }
  .footer { left: 0; top: 1041px; width: 760px; height: 81px; background: var(--navy); color: var(--white); }
  .address { left: 21px; top: 11px; font-size: 17px; font-weight: 600; display: flex; align-items: center; gap: 8px; }
  .phone { left: 24px; top: 40px; font-size: 26px; font-weight: 700; display: flex; align-items: center; gap: 8px; }
  .social { left: 525px; top: 29px; font-size: 17px; font-weight: 500; display: flex; align-items: center; gap: 8px; }
  .social .square { width: 26px; height: 26px; border-radius: 5px; background: var(--white); }
</style>
</head>
<body>
<div class="poster">
  <div class="abs backdrop" role="img" aria-label="Faded school mascot artwork over light math sketches"></div>

  <div class="abs year">2021-22</div>
  <div class="abs title-band"></div>
  <div class="abs title">PRIORITY GOALS</div>
  <div class="abs intro-band"></div>
  <p class="abs intro">We will accelerate the academic &amp; Social/Emotional Growth of the students we serve by:</p>

  <div class="abs school-mark">
    <span class="dot"></span>
    <span class="name">CEDAR RIDGE<br>ELEMENTARY<br>SCHOOL</span>
  </div>

  <svg class="abs wheel" width="760" height="1158" viewBox="0 0 760 1158" xmlns="http://www.w3.org/2000/svg">
    <circle cx="379" cy="577" r="342" fill="var(--ring)"/>
    <circle cx="379" cy="577" r="334" fill="var(--white)"/>
    <g transform="translate(379 577)">
      <defs>
        <path id="wedge" d="M0 0 Q137.9 -115.7 323 0 A323 323 0 0 1 228.4 228.4 Q179.3 15.7 0 0 Z"/>
      </defs>
      <use href="#wedge" transform="rotate(-90)" fill="var(--blue-dark)"/>
      <use href="#wedge" transform="rotate(-45)" fill="var(--yellow)"/>
      <use href="#wedge" transform="rotate(0)" fill="var(--blue-dark)"/>
      <use href="#wedge" transform="rotate(45)" fill="var(--yellow)"/>
      <use href="#wedge" transform="rotate(90)" fill="var(--blue-light)"/>
      <use href="#wedge" transform="rotate(135)" fill="var(--blue-dark)"/>
      <use href="#wedge" transform="rotate(180)" fill="var(--yellow)"/>
      <use href="#wedge" transform="rotate(225)" fill="var(--blue-light)"/>
    </g>
    <rect x="330" y="402" width="98" height="90" rx="14" fill="var(--navy)" role="img" aria-label="Graduate figure in cap"/>
    <path class="heart" d="M379 510 C350 470 254 475 256 545 C258 600 340 650 379 697 C418 650 500 600 502 545 C504 475 408 470 379 510 Z" fill="var(--white)" stroke="#dcdcdc" stroke-width="6"/>
    <rect x="300" y="525" width="158" height="112" rx="10" fill="#e6e9f4" role="img" aria-label="Icons of a teacher with students, a school building and a connected team"/>
  </svg>

  <div class="abs goal on-dark voices">
    <p>Voices of <span class="tag-dark">All</span></p>
    <p>Who are we?</p>
    <p>Where are we<br>going?</p>
  </div>
  <p class="abs goal on-dark broaden">Broaden our Lead</p>
  <div class="abs goal on-yellow staff">
    <p>Staff doing what<br>they Love...</p>
    <p>Teaching kids for<br>Proven Growth</p>
  </div>
  <div class="abs goal on-dark communicate">
    <p>Communicate,<br>Communicate,<br>Communicate,</p>
    <ul>
      <li><span class="tag-light">Expectations</span></li>
      <li>Support</li>
      <li>For Clarity</li>
    </ul>
  </div>
  <div class="abs goal on-yellow build">
    <p><strong>Build Value</strong></p>
    <p><strong class="tag-light">Partnership</strong></p>
    <ul>
      <li>Correct</li>
      <li>Celebrate</li>
      <li>Strong, Predictable</li>
      <li>Laugh,Have Fun</li>
    </ul>
  </div>
  <div class="abs goal on-dark wellness">
    <p><span class="tag-dark">Wellness</span></p>
    <p>Mental Health for every<br>person in our school<br>community</p>
  </div>
  <p class="abs goal on-dark intentional">Be intentional with<br>each action- Focus</p>
  <p class="abs goal on-yellow small-steps">Small Measured<br>Step Towards<br>Larger Goal</p>

  <h2 class="abs promises">FOUNDATIONAL PROMISES</h2>
  <p class="abs promises-sub">( 4 YEARS STRONG, BETTER EVERYDAY )</p>

  <div class="abs footer-strip"></div>
  <div class="abs footer">
    <div class="abs address">
      <svg width="16" height="21" viewBox="0 0 16 21"><path d="M8 0 C3.6 0 0 3.4 0 7.7 C0 13 8 21 8 21 S16 13 16 7.7 C16 3.4 12.4 0 8 0 Z M8 4.3 A3.4 3.4 0 1 1 8 11.1 A3.4 3.4 0 1 1 8 4.3 Z" fill="var(--white)" fill-rule="evenodd"/></svg>
      1480 Birchwood Ave., Pine Hollow, WA 98000
    </div>
    <div class="abs phone">
      <svg width="12" height="20" viewBox="0 0 12 20"><path d="M4 1 L7 5 L5 7 C5 10 6 13 8 14 L10 12.5 L12 16.5 L9 19 C3 17 0 8 4 1 Z" fill="var(--white)"/></svg>
      555-014-2600
    </div>
    <div class="abs social">
      <span class="square"></span>
      @cedarridgelearners
    </div>
  </div>
</div>
</body>
</html>
```